i would like a business card to leave with customers and potential customers for electrical work and for the supply and install of reverse cycle airconditioning in the domestic and commercial market.
I own my own business and im a sole trader. I have an a'class electrical lisence and also a refrigeration lisence so i am
able to offer complete installations in airconditioning by a fully qualified and lisenced tradesman.
im looking for something that comes across as unique and professional.
i had the coluor black and some gold in mind but open to any coluors.
something like Lanterra Electrical & Refrigeration
or Lanterra Air.
i will use this design on a business card to advertise through summer to help generate installs through the busy season.

Target Market(s)

Mainly domestic house holds through summer who are in need of airconditioning and reliable information to acomadate thier cooling and heating requirements

Industry/Entity Type

Electrical

Requirements
Must have
• Business name- Lanterra
My name- Mark Delford
My mobile no- 0438 517 290
My email- mrdelford@qelvo.com.au
Installation & Decomissioning of aiconditioning split systems
LIC NO: TRK 540316
Nice to have
• Lanterra Electrical & Refrigeration

```html
<!DOCTYPE html>
<html lang="en">
<head>
<meta charset="utf-8">
<title>Lanterra Electrical &amp; Refrigeration – Business Card</title>
<link rel="stylesheet" href="https://fonts.googleapis.com/css2?family=Kaushan+Script&family=Open+Sans:wght@600;700&family=Arimo:wght@700&display=swap">
<style>
  :root {
    --backdrop: #e4e7e8;
    --gold: #dccb00;
    --ink: #0b0b0b;
    --paper: #ffffff;
    --sky: #2aa9e8;
    --badge-blue: #6fe0f8;
    --badge-green: #b8f21c;
  }
  * { margin: 0; padding: 0; box-sizing: border-box; }
  html, body { width: 1200px; height: 900px; overflow: hidden; }
  body {
    position: relative;
    background: var(--backdrop);
    font-family: "Open Sans", Arial, sans-serif;
  }
  .card {
    position: absolute;
    top: 57px;
    width: 450px;
    height: 783px;
    border-radius: 26px;
    overflow: hidden;
  }

  /* Front */
  .card--front { left: 100px; background: var(--gold); color: var(--ink); }
  .front__strip {
    position: absolute; left: 0; top: 0;
    width: 43px; height: 400px;
    background: var(--ink);
  }
  .front__email {
    position: absolute;
    left: 30px; top: 743px;
    transform-origin: left top;
    transform: rotate(-90deg);
    font-size: 19px; font-weight: 600; letter-spacing: 1.5px;
    white-space: nowrap;
  }
  .front__brand {
    position: absolute; left: 120px; top: 110px;
    display: flex; align-items: center; gap: 12px;
    font-size: 40px; font-weight: 700; color: var(--sky);
  }
  .front__brand-dot {
    width: 26px; height: 26px; border-radius: 50%; background: var(--sky);
  }
  .front__script {
    position: absolute; left: 72px; top: 285px;
    font-family: "Kaushan Script", cursive;
    font-size: 100px; line-height: 1;
    white-space: nowrap;
  }
  .front__company {
    position: absolute; left: 212px; top: 415px;
    font-size: 18px; font-weight: 700; line-height: 1.35;
  }
  .front__contact {
    position: absolute; right: 32px; top: 690px;
    text-align: center;
  }
  .front__name {
    font-family: "Arimo", Arial, sans-serif;
    font-size: 31px; font-weight: 700;
  }
  .front__phone { font-size: 19px; font-weight: 700; letter-spacing: 0.5px; margin-top: 4px; }

  /* Back */
  .card--back { left: 650px; background: var(--ink); color: var(--paper); }
  .back__service {
    position: absolute; left: 32px; top: 28px;
    font-size: 18px; font-weight: 700; line-height: 1.3;
    z-index: 1;
  }
  .back__script {
    position: absolute; left: 356px; top: 438px;
    transform: translate(-50%, -50%) rotate(-90deg);
    font-family: "Kaushan Script", cursive;
    font-size: 205px; line-height: 1;
    color: var(--gold);
    white-space: nowrap;
  }
  .back__badge { position: absolute; left: 88px; top: 584px; }
  .back__licence {
    position: absolute; left: 32px; top: 730px;
    font-size: 20px; font-weight: 700; letter-spacing: 0.5px;
  }
</style>
</head>
<body>
  <section class="card card--front">
    <div class="front__strip"></div>
    <p class="front__email">mrdelford@qelvo.com.au</p>
    <div class="front__brand"><span class="front__brand-dot"></span>Lanterra</div>
    <p class="front__script">Lanterra</p>
    <p class="front__company">Lanterra Electrical<br>&amp; Refrigeration</p>
    <div class="front__contact">
      <p class="front__name">Mark Delford</p>
      <p class="front__phone">0438 517 290</p>
    </div>
  </section>

  <section class="card card--back">
    <p class="back__service">Installation &amp; Decommissioning<br>of air-conditioning split systems</p>
    <p class="back__script">Lanterra</p>
    <svg class="back__badge" width="98" height="98" viewBox="0 0 98 98" role="img" aria-label="Authorisation badge">
      <rect width="98" height="98" fill="var(--badge-blue)"/>
      <rect y="58" width="98" height="40" fill="var(--badge-green)"/>
    </svg>
    <p class="back__licence">LIC NO: TRK 540316</p>
  </section>
</body>
</html>
```